Quillbrook Air Business Card Design

Design new, 2 sides, business cards for a residential and light commercial heating, air conditioning contractor.

Target Market(s)

Homeowners, small businesses

Industry/Entity Type

Business

Contact Information for Business Card

Dominic Westerhall
Phone - 862-415-2736
Email
Address - PO box 518
Brightwater NJ 07912
Website - www.HarborBreezeLLC.example

Requirements
Must have
• logo, company colors, standard size with no die cut, so I can use nova stamp

```html
<!DOCTYPE html>
<html lang="en">
<head>
<meta charset="utf-8">
<title>Quillbrook Air Business Card</title>
<link href="https://fonts.googleapis.com/css2?family=Josefin+Sans:wght@400;600&family=Lato:wght@400&display=swap" rel="stylesheet">
<style>
  :root {
    --maroon: #a3213a;
    --maroon-dark: #861a2f;
    --orange: #f08a24;
    --cream: #fde9a0;
    --white: #ffffff;
    --stage: #d9d3ca;
  }
  * { box-sizing: border-box; margin: 0; padding: 0; }
  html, body { width: 1200px; height: 950px; overflow: hidden; }
  body {
    background: var(--stage);
    display: flex;
    flex-direction: column;
    align-items: center;
    justify-content: center;
    gap: 50px;
  }
  .card {
    width: 700px;
    height: 400px;
    position: relative;
    overflow: hidden;
    box-shadow: 0 6px 18px rgba(0,0,0,.18);
  }

  /* Front */
  .card-front {
    background: var(--white);
    display: flex;
    align-items: center;
    justify-content: center;
    gap: 18px;
  }
  .brand-dot {
    width: 34px; height: 34px;
    border-radius: 50%;
    background: var(--orange);
  }
  .brand-name {
    font-family: "Josefin Sans", sans-serif;
    font-weight: 600;
    font-size: 54px;
    letter-spacing: 2px;
    text-transform: uppercase;
    color: var(--maroon);
    white-space: nowrap;
  }

  /* Back */
  .card-back { background: var(--maroon); }
  .band {
    position: absolute;
    top: 0; bottom: 0;
    left: 150px;
    width: 46px;
    background: var(--orange);
  }
  .nameplate {
    position: absolute;
    left: 58px; top: 115px;
    width: 230px; height: 170px;
  }
  .nameplate svg { position: absolute; inset: 0; }
  .nameplate-text {
    position: absolute;
    inset: 0;
    display: flex;
    flex-direction: column;
    align-items: center;
    justify-content: center;
    color: var(--white);
    text-align: center;
    font-family: "Josefin Sans", sans-serif;
  }
  .person-name { font-size: 22px; font-weight: 400; letter-spacing: 1px; text-transform: uppercase; line-height: 1.15; }
  .person-title { font-size: 13px; letter-spacing: 2px; margin-top: 6px; text-transform: uppercase; }

  .contact-list {
    position: absolute;
    left: 350px; top: 58px;
    list-style: none;
    display: flex;
    flex-direction: column;
    gap: 14px;
    font-family: "Lato", sans-serif;
    font-size: 15px;
    color: var(--white);
  }
  .contact-item { display: flex; align-items: center; gap: 14px; line-height: 1.3; white-space: nowrap; }
  .contact-icon {
    flex: none;
    width: 30px; height: 30px;
    border-radius: 50%;
    background: var(--cream);
    display: flex; align-items: center; justify-content: center;
  }
  .contact-icon svg { width: 18px; height: 18px; fill: var(--maroon); }
</style>
</head>
<body>

<section class="card card-front" aria-label="Card front">
  <span class="brand-dot"></span>
  <span class="brand-name">Quillbrook Air</span>
</section>

<section class="card card-back" aria-label="Card back">
  <div class="band"></div>

  <div class="nameplate">
    <svg viewBox="0 0 230 170" aria-hidden="true">
      <path d="M40 20 Q115 -4 190 20 Q192 42 214 44 L214 126 Q192 128 190 150 Q115 174 40 150 Q38 128 16 126 L16 44 Q38 42 40 20 Z"
            fill="var(--maroon)" stroke="var(--orange)" stroke-width="6"/>
      <path d="M46 30 Q115 9 184 30 Q186 50 204 52 L204 118 Q186 120 184 140 Q115 161 46 140 Q44 120 26 118 L26 52 Q44 50 46 30 Z"
            fill="none" stroke="var(--white)" stroke-width="2"/>
    </svg>
    <div class="nameplate-text">
      <span class="person-name">Dominic<br>Westerhall</span>
      <span class="person-title">President</span>
    </div>
  </div>

  <ul class="contact-list">
    <li class="contact-item">
      <span class="contact-icon"><svg viewBox="0 0 24 24"><path d="M12 2a7 7 0 0 0-7 7c0 5 7 13 7 13s7-8 7-13a7 7 0 0 0-7-7zm0 9.5A2.5 2.5 0 1 1 12 6.5a2.5 2.5 0 0 1 0 5z"/></svg></span>
      <span>PO box 518<br>Brightwater NJ 07912</span>
    </li>
    <li class="contact-item">
      <span class="contact-icon"><svg viewBox="0 0 24 24"><path d="M6.6 10.8a15 15 0 0 0 6.6 6.6l2.2-2.2a1 1 0 0 1 1-.25 11 11 0 0 0 3.6.6 1 1 0 0 1 1 1V20a1 1 0 0 1-1 1A17 17 0 0 1 3 4a1 1 0 0 1 1-1h3.5a1 1 0 0 1 1 1 11 11 0 0 0 .6 3.6 1 1 0 0 1-.25 1z"/></svg></span>
      <span>862 415 2736</span>
    </li>
    <li class="contact-item">
      <span class="contact-icon"><svg viewBox="0 0 24 24"><path d="M7 2h10a1 1 0 0 1 1 1v18a1 1 0 0 1-1 1H7a1 1 0 0 1-1-1V3a1 1 0 0 1 1-1zm1 3v12h8V5zm4 13.5a1 1 0 1 0 0 2 1 1 0 0 0 0-2z"/></svg></span>
      <span>862 415 2740</span>
    </li>
    <li class="contact-item">
      <span class="contact-icon"><svg viewBox="0 0 24 24"><path d="M6 2h9l3 3v4H6zM4 10h16a1 1 0 0 1 1 1v7h-3v4H6v-4H3v-7a1 1 0 0 1 1-1zm4 6v4h8v-4z"/></svg></span>
      <span>862 415 2744</span>
    </li>
    <li class="contact-item">
      <span class="contact-icon"><svg viewBox="0 0 24 24"><path d="M3 5h18a1 1 0 0 1 1 1v12a1 1 0 0 1-1 1H3a1 1 0 0 1-1-1V6a1 1 0 0 1 1-1zm1 2.3V17h16V7.3l-8 5.2z M5 7l7 4.5L19 7z"/></svg></span>
      <span>dominic@quillbrookair.example</span>
    </li>
    <li class="contact-item">
      <span class="contact-icon"><svg viewBox="0 0 24 24"><path d="M12 2a10 10 0 1 0 0 20 10 10 0 0 0 0-20zm6.9 9h-3a15 15 0 0 0-1.4-6A8 8 0 0 1 18.9 11zM12 4.1c.9 1.3 1.7 3.7 1.9 6.9h-3.8c.2-3.2 1-5.6 1.9-6.9zM9.5 5a15 15 0 0 0-1.4 6h-3A8 8 0 0 1 9.5 5zM5.1 13h3a15 15 0 0 0 1.4 6A8 8 0 0 1 5.1 13zm6.9 6.9c-.9-1.3-1.7-3.7-1.9-6.9h3.8c-.2 3.2-1 5.6-1.9 6.9zm2.5-.9a15 15 0 0 0 1.4-6h3a8 8 0 0 1-4.4 6z"/></svg></span>
      <span>www.QuillbrookAirLLC.example</span>
    </li>
  </ul>
</section>

</body>
</html>
```